Our companies name is The Gilded Ladle and we specialize in craft cupcakes, what I mean by that is that we bake our cupcakes with craft beer and other alcoholic drinks. We are trying to focus on being elegant but at the same time unpretentious. Since we are incorporating beer in our cupcakes we want the business card to have our logo in the front and our information in the back.

Once we select the best design we will provide the contact information to be added. Thank you.

Industry/Entity Type

Business

Font styles to use
Decorative
Script

Requirements
Must have
• Round corners
Should not have
• Square corners

```html
<!DOCTYPE html>
<html lang="en">
<head>
<meta charset="utf-8">
<title>The Gilded Ladle — Business Card</title>
<link rel="stylesheet" href="https://fonts.googleapis.com/css2?family=Saira:wght@400;500;600&display=swap">
<style>
  :root {
    --bg: #e9e6e1;
    --teal: #86cfc4;
    --white: #f7f7f7;
    --silver-light: #ececec;
    --silver-dark: #9a9a9a;
    --red: #e8262e;
    --ink: #2b2b2b;
    --ink-soft: #555555;
  }
  * { box-sizing: border-box; margin: 0; padding: 0; }
  html, body { width: 1200px; height: 828px; overflow: hidden; }
  body {
    background: var(--bg);
    font-family: "Saira", Arial, sans-serif;
    position: relative;
  }
  .card {
    position: absolute;
    width: 540px;
    height: 310px;
    border-radius: 18px;
    overflow: hidden;
    background: var(--white);
    box-shadow: 0 6px 18px rgba(0,0,0,0.18);
  }
  .card--front { left: 40px; top: 259px; }
  .card--back  { left: 620px; top: 259px; }
  .card__art { position: absolute; inset: 0; width: 100%; height: 100%; }

  .brand {
    position: absolute;
    display: flex;
    align-items: center;
    gap: 10px;
  }
  .brand__dot {
    width: 22px; height: 22px;
    border-radius: 50%;
    background: var(--red);
  }
  .brand__name {
    font-family: "Saira", Arial, sans-serif;
    font-weight: 600;
    font-size: 20px;
    letter-spacing: 0.5px;
    color: var(--ink);
  }
  .card--front .brand { left: 60px; top: 192px; }
  .card--back .brand { left: 48px; top: 112px; }

  .person {
    position: absolute;
    right: 40px;
    top: 34px;
    text-align: right;
  }
  .person__name {
    color: var(--red);
    font-size: 22px;
    font-weight: 500;
    letter-spacing: 1px;
    text-transform: uppercase;
    line-height: 1;
  }
  .person__role {
    color: var(--ink-soft);
    font-size: 10px;
    letter-spacing: 1.5px;
    text-transform: uppercase;
    margin-top: 4px;
  }

  .address {
    position: absolute;
    right: 32px;
    top: 192px;
    text-align: right;
    color: var(--white);
    font-size: 14px;
    line-height: 1.4;
  }

  .contacts {
    position: absolute;
    left: 172px;
    bottom: 16px;
    list-style: none;
    color: var(--white);
    font-size: 11px;
    line-height: 1;
  }
  .contacts li {
    display: flex;
    align-items: center;
    gap: 8px;
    margin-top: 4px;
  }
  .contacts svg { width: 11px; height: 11px; flex: none; }
</style>
</head>
<body>

  <section class="card card--front" aria-label="Card front">
    <svg class="card__art" viewBox="0 0 540 310" preserveAspectRatio="none" aria-hidden="true">
      <defs>
        <linearGradient id="frontSilver" x1="0" y1="1" x2="1" y2="0">
          <stop offset="0" stop-color="var(--silver-light)"/>
          <stop offset="0.45" stop-color="var(--silver-dark)"/>
          <stop offset="1" stop-color="var(--silver-light)"/>
        </linearGradient>
        <linearGradient id="frontWhite" x1="0" y1="0" x2="1" y2="1">
          <stop offset="0" stop-color="#e3e3e3"/>
          <stop offset="1" stop-color="#fafafa"/>
        </linearGradient>
      </defs>
      <rect width="540" height="310" fill="var(--teal)"/>
      <path d="M0,200 C120,150 300,90 540,20 L540,310 L0,310 Z" fill="var(--red)"/>
      <path d="M0,222 C130,165 320,100 540,40 L540,310 L0,310 Z" fill="url(#frontSilver)"/>
      <path d="M0,236 C140,178 330,112 540,52 L540,310 L0,310 Z" fill="url(#frontWhite)"/>
    </svg>
    <div class="brand">
      <span class="brand__dot"></span>
      <span class="brand__name">The Gilded Ladle</span>
    </div>
  </section>

  <section class="card card--back" aria-label="Card back">
    <svg class="card__art" viewBox="0 0 540 310" preserveAspectRatio="none" aria-hidden="true">
      <defs>
        <linearGradient id="backSilver" x1="0" y1="1" x2="1" y2="0">
          <stop offset="0" stop-color="var(--silver-light)"/>
          <stop offset="0.5" stop-color="var(--silver-dark)"/>
          <stop offset="1" stop-color="var(--silver-light)"/>
        </linearGradient>
      </defs>
      <rect width="540" height="310" fill="var(--white)"/>
      <path d="M0,300 C50,225 140,180 260,160 C380,137 470,100 540,66 L540,310 L0,310 Z" fill="var(--red)"/>
      <path d="M10,306 C60,233 145,193 260,173 C380,150 470,115 540,84 L540,310 L10,310 Z" fill="url(#backSilver)"/>
      <path d="M30,310 C70,240 150,205 260,185 C380,162 470,128 540,98 L540,310 Z" fill="var(--teal)"/>
    </svg>

    <div class="brand">
      <span class="brand__dot"></span>
      <span class="brand__name">The Gilded Ladle</span>
    </div>

    <div class="person">
      <p class="person__name">Mara Ellison</p>
      <p class="person__role">Managing Director</p>
    </div>

    <p class="address">27 Copper Lane Suite 4<br>Harbor Quarter</p>

    <ul class="contacts">
      <li>
        <svg viewBox="0 0 12 12"><path d="M2 1 L4.5 1 L5 4 L3.6 5 Q4.8 7.4 7 8.4 L8 7 L11 7.5 L11 10 Q6 11 2.5 6.5 Q1 4 2 1 Z" fill="var(--red)"/></svg>
        014 552 0187
      </li>
      <li>
        <svg viewBox="0 0 12 12"><rect x="3" y="0.5" width="6" height="11" rx="1" fill="none" stroke="var(--red)" stroke-width="1.2"/><circle cx="6" cy="9.5" r="0.7" fill="var(--red)"/></svg>
        014 552 0188
      </li>
      <li>
        <svg viewBox="0 0 12 12"><rect x="1" y="4" width="10" height="6" fill="var(--red)"/><rect x="3" y="1" width="6" height="3" fill="var(--red)"/></svg>
        014 552 0189
      </li>
      <li>
        <svg viewBox="0 0 12 12"><rect x="0.5" y="2" width="11" height="8" fill="var(--red)"/><path d="M0.5 2 L6 6.5 L11.5 2" fill="none" stroke="var(--white)" stroke-width="1"/></svg>
        hello@gildedladle.com
      </li>
      <li>
        <svg viewBox="0 0 12 12"><circle cx="6" cy="6" r="5.5" fill="var(--red)"/><path d="M0.5 6 H11.5 M6 0.5 V11.5 M6 0.5 Q2.5 6 6 11.5 M6 0.5 Q9.5 6 6 11.5" fill="none" stroke="var(--white)" stroke-width="0.7"/></svg>
        www.gildedladle.com
      </li>
    </ul>
  </section>

</body>
</html>
```